Sustainably Transforming Education

Company is education services based. early learning through adult and corporate. Focus is national government policy and program design and delivery alongside a research based and academically grounded set of approaches to planning, evaluation, and change management.I am looking for an innovative design position that aligns with the global agendas for innovation, creativity and collaboration at international and national policy levels (berulo is a name that reflects these qualities - colours need to reflect amythyst in some way). I also need a design that translates from a business card as 1 medium of interaction to a template that can work in word/powerpoint etc to support both stationery as well as a digital strategy across multiple channels (fb/twit/etc)There is no slogan/tag line for the company and their is no logo. I was looking to just leverage the name - have currently played around with various fonts (ending up with cuisine - all lowercase).

Industry/Entity Type

Adult

Contact Information for Business Card

name: berulo (all lowercase)Chairman: Andrew CrowMobile: +61 418 902 131Web: www.berulo.comemail: martin.pelly@berulo-example.com

Font styles to use
Script
Other font styles liked:
• cuisine

Colors
e34298
e667a6
33a6d7
aaaaaa

Requirements
Nice to have
• https://files.example-share.net/sh/qx7kw2hd91lzmnp/AAFr3tYbQeLp8VwZnKcDs2Hu?dl=0
• Link to the printwell templates used to begin this process....the one with the lines was about people intersecting (collaborating).....the organic shapes one more of a fluid feel of people coming together - the overall shape being largely spherical could represent a "global" feel.....anyway that is how I was thinking about these

```html
<!DOCTYPE html>
<html lang="en">
<head>
<meta charset="utf-8">
<title>berulo – Business Card</title>
<link href="https://fonts.googleapis.com/css2?family=Kaushan+Script&display=swap" rel="stylesheet">
<style>
  :root {
    --amethyst-pink: #e34298;
    --soft-pink: #e667a6;
    --sky-blue: #33a6d7;
    --rule-blue: #1f98d3;
    --map-blue: #72b8e2;
    --silver: #aaaaaa;
    --white: #ffffff;
    --ink: #1a1a1a;
  }
  html, body {
    margin: 0;
    padding: 0;
    width: 1200px;
    height: 740px;
    overflow: hidden;
    background: var(--amethyst-pink);
  }
  .card {
    position: relative;
    width: 1200px;
    height: 740px;
    overflow: hidden;
    font-family: "Kaushan Script", cursive;
    color: var(--white);
  }
  .card__backdrop {
    position: absolute;
    inset: 0;
    width: 1200px;
    height: 740px;
  }
  .backdrop__base { fill: var(--amethyst-pink); }
  .backdrop__swoosh { fill: var(--soft-pink); }
  .backdrop__corner { fill: var(--amethyst-pink); }
  .backdrop__stripe { fill: var(--silver); }
  .backdrop__wave { fill: var(--sky-blue); }
  .card__world-map {
    position: absolute;
    left: 326px;
    top: 128px;
    width: 744px;
    height: 436px;
    border-radius: 60px 90px 70px 120px;
    background: radial-gradient(ellipse at 50% 45%, rgba(140, 200, 235, 0.75), rgba(114, 184, 226, 0.35) 70%, rgba(114, 184, 226, 0) 100%);
  }
  .person {
    position: absolute;
    left: 324px;
    top: 88px;
  }
  .person__name {
    margin: 0;
    font-size: 74px;
    line-height: 1;
    font-weight: 400;
    color: var(--white);
  }
  .person__role {
    margin: 4px 0 0 4px;
    font-size: 40px;
    line-height: 1;
    font-weight: 400;
    color: var(--ink);
  }
  .person__rule {
    position: absolute;
    left: 326px;
    top: 227px;
    width: 760px;
    height: 3px;
    background: var(--rule-blue);
  }
  .contact {
    position: absolute;
    left: 622px;
    top: 322px;
    margin: 0;
    padding: 0;
    list-style: none;
  }
  .contact__item {
    display: flex;
    align-items: center;
    height: 46px;
    font-size: 24px;
    letter-spacing: 0.5px;
  }
  .contact__icon {
    width: 28px;
    height: 28px;
    margin-right: 16px;
    flex: none;
    fill: var(--amethyst-pink);
    stroke: var(--amethyst-pink);
  }
  .brand {
    position: absolute;
    left: 102px;
    top: 520px;
    margin: 0;
    font-size: 84px;
    line-height: 1;
    font-weight: 400;
    color: var(--white);
  }
</style>
</head>
<body>
  <main class="card">
    <svg class="card__backdrop" viewBox="0 0 1000 617" preserveAspectRatio="none" aria-hidden="true">
      <rect class="backdrop__base" x="0" y="0" width="1000" height="617"/>
      <path class="backdrop__swoosh" d="M540,0 L1000,0 L1000,480 C980,300 900,150 780,80 C700,35 620,15 540,0 Z"/>
      <path class="backdrop__corner" d="M630,0 L1000,0 L1000,125 C900,60 790,20 630,0 Z"/>
      <path class="backdrop__stripe" d="M62,0 L112,0 C165,150 300,380 480,520 C560,580 630,605 720,617 L590,617 C470,565 335,455 232,305 C162,205 102,92 62,0 Z"/>
      <path class="backdrop__wave" d="M98,0 L560,0 C700,20 820,70 880,140 C950,230 985,380 1000,540 C990,580 975,600 960,617 L690,617 C565,592 435,505 332,382 C232,262 152,132 98,0 Z"/>
    </svg>

    <div class="card__world-map" role="img" aria-label="Faint world map spread across the blue wave"></div>

    <header class="person">
      <h1 class="person__name">Martin Pelly</h1>
      <p class="person__role">Chairman</p>
    </header>
    <div class="person__rule"></div>

    <ul class="contact">
      <li class="contact__item">
        <svg class="contact__icon" viewBox="0 0 24 24" aria-hidden="true">
          <path stroke="none" d="M3 7c0-2 2-3 9-3s9 1 9 3v2h-4V7.5c-1-.5-3-.8-5-.8s-4 .3-5 .8V9H3z"/>
          <path stroke="none" d="M6 10h12l2 10H4z"/>
          <circle cx="12" cy="15" r="2.4" fill="#33a6d7" stroke="none"/>
        </svg>
        <span>+61 427 315 086</span>
      </li>
      <li class="contact__item">
        <svg class="contact__icon" viewBox="0 0 24 24" aria-hidden="true">
          <rect x="2" y="5" width="20" height="14" stroke="none"/>
          <path d="M2.5 5.5 L12 13 L21.5 5.5 M2.5 18.5 L9.5 11.5 M21.5 18.5 L14.5 11.5" fill="none" stroke="#33a6d7" stroke-width="1.4"/>
        </svg>
        <span>martin.pelly@berulo-example.com</span>
      </li>
      <li class="contact__item">
        <svg class="contact__icon" viewBox="0 0 24 24" aria-hidden="true">
          <g fill="none" stroke-width="1.8">
            <circle cx="12" cy="12" r="9.5"/>
            <ellipse cx="12" cy="12" rx="4.2" ry="9.5"/>
            <path d="M2.5 12h19M4 7h16M4 17h16"/>
          </g>
        </svg>
        <span>www.berulo-example.com</span>
      </li>
    </ul>

    <p class="brand">berulo</p>
  </main>
</body>
</html>
```